Business Card Design Project - del varosi group

dear Sirs

we need business card design for our group ( DEL Varosi Group ) , i have got the Logo design of our group from pixel harbor in previous , so all need details relating to our group i think available with you, as well as the the chosen logo design

we hope to provide us with business card logo that to be appropaite and satisfactory to us .

thanks

note : logo design of our group is attached .
Updates

Reason: please extend the deadline of my project for additional 15 days because i didn't received appropriate design for our gruop yet . kindly beaware that i have received 77 design till now , supossed to send me 200-250 design at least . thanks

Target Market(s)

contents

name : Kerem EL Nadiri

position : Operation Manager

Industry/Entity Type

Business

Requirements
Must have

• person name

group logo
Nice to have
• logo color matching with back background

```html
<!DOCTYPE html>
<html lang="en">
<head>
<meta charset="utf-8">
<title>DEL Varosi Group – Business Card</title>
<link href="https://fonts.googleapis.com/css2?family=Open+Sans:wght@400;600;700&display=swap" rel="stylesheet">
<style>
  :root {
    --backdrop: #f1e9d2;
    --gold-light: #e2b562;
    --gold: #c9973d;
    --gold-deep: #a9782b;
    --gold-glow: rgba(250, 228, 170, 0.55);
    --navy: #1f3f78;
    --ink: #2f2f2f;
    --muted: #555555;
    --card-white: #ffffff;
  }
  * { margin: 0; padding: 0; box-sizing: border-box; }
  html, body {
    width: 1200px; height: 951px; overflow: hidden;
    background: var(--backdrop);
    font-family: "Open Sans", Arial, sans-serif;
  }
  .stage { position: relative; width: 1200px; height: 951px; }

  .card {
    position: absolute;
    width: 580px; height: 330px;
    border-radius: 22px;
    overflow: hidden;
    box-shadow: 0 10px 28px rgba(90, 70, 30, 0.25);
  }

  /* Front side */
  .card--front {
    left: 70px; top: 90px;
    background: linear-gradient(135deg, var(--gold-light) 0%, var(--gold) 55%, var(--gold-deep) 100%);
  }
  .card--front .sheen {
    position: absolute; right: 0; top: 0;
    width: 340px; height: 170px;
    background: radial-gradient(ellipse at 100% 0%, var(--gold-glow) 0%, rgba(250, 228, 170, 0) 70%);
  }
  .card--front .brand {
    position: absolute; left: 0; right: 0; top: 150px;
    text-align: center;
  }

  .brand-name {
    display: inline-flex; align-items: center; gap: 12px;
    font-weight: 700; color: var(--navy);
    letter-spacing: 1px; text-transform: uppercase;
  }
  .brand-name .mark {
    width: 18px; height: 18px; background: var(--navy);
  }
  .card--front .brand-name { font-size: 44px; }
  .card--back .brand-name { font-size: 36px; }

  /* Back side */
  .card--back {
    left: 550px; top: 500px;
    background: var(--card-white);
  }
  .card--back .brand {
    position: absolute; left: 0; right: 0; top: 50px;
    text-align: center;
  }
  .person { position: absolute; left: 60px; top: 145px; }
  .person-name { font-size: 22px; font-weight: 600; color: var(--ink); letter-spacing: 0.5px; }
  .person-role { font-size: 15px; color: var(--gold); margin-top: 2px; }

  .address {
    position: absolute; left: 60px; top: 212px;
    display: flex; gap: 10px;
    font-size: 15px; line-height: 21px; color: var(--muted);
  }
  .contacts {
    position: absolute; left: 330px; top: 212px;
    list-style: none;
    font-size: 15px; line-height: 21px; color: var(--muted);
  }
  .contacts li { display: flex; align-items: center; gap: 9px; white-space: nowrap; }
  .contacts .accent { color: var(--gold); }
  .icon { width: 14px; height: 14px; flex: none; fill: var(--gold); }
  .address .icon { margin-top: 3px; }

  .base-band { position: absolute; left: 0; bottom: 0; width: 100%; height: 26px; }
</style>
</head>
<body>
<main class="stage">

  <section class="card card--front" aria-label="Business card front">
    <div class="sheen" role="img" aria-label="Soft light gold swoosh decoration"></div>
    <div class="brand">
      <span class="brand-name"><span class="mark"></span>DEL Varosi Group</span>
    </div>
  </section>

  <section class="card card--back" aria-label="Business card back">
    <div class="brand">
      <span class="brand-name"><span class="mark"></span>DEL Varosi Group</span>
    </div>

    <div class="person">
      <p class="person-name">Kerem EL Nadiri</p>
      <p class="person-role">Operation Manager</p>
    </div>

    <div class="address">
      <svg class="icon" viewBox="0 0 16 16" aria-hidden="true"><path d="M8 1 L15 8 H13 V15 H9.5 V10.5 H6.5 V15 H3 V8 H1 Z"/></svg>
      <p>4150 Larkmoor Ave.<br>Suite 210-84<br>Denton, TX 76201</p>
    </div>

    <ul class="contacts">
      <li><svg class="icon" viewBox="0 0 16 16" aria-hidden="true"><path d="M4 1 L6.5 4.5 L5 6.5 C6 8.5 7.5 10 9.5 11 L11.5 9.5 L15 12 L13.5 15 C7 14.5 1.5 9 1 2.5 Z"/></svg><span>940-555-0182</span></li>
      <li><svg class="icon" viewBox="0 0 16 16" aria-hidden="true"><path d="M4 1 H12 V5 H4 Z M1 6 H15 V12 H12 V15 H4 V12 H1 Z M5.5 10 V13.5 H10.5 V10 Z"/></svg><span>940-555-0183</span></li>
      <li><svg class="icon" viewBox="0 0 16 16" aria-hidden="true"><path d="M1 3 H15 V13 H1 Z M2 4.2 L8 9 L14 4.2 Z" fill-rule="evenodd"/></svg><span>info@<span class="accent">delvarosigroup</span>.com</span></li>
      <li><svg class="icon" viewBox="0 0 16 16" aria-hidden="true"><circle cx="8" cy="8" r="7"/></svg><span>www.<span class="accent">delvarosigroup</span>.com</span></li>
    </ul>

    <svg class="base-band" viewBox="0 0 580 26" preserveAspectRatio="none" aria-hidden="true">
      <path d="M0 10 C150 4 300 2 420 8 L420 26 L0 26 Z" fill="var(--navy)"/>
      <path d="M380 6 C460 2 530 2 580 6 L580 26 L360 26 Z" fill="var(--gold)"/>
    </svg>
  </section>

</main>
</body>
</html>
```